BrimFalcon Business Cards

We have a defined brand. Please visit our website to get a feel for the product and the color pallets. www.brimfalcon-example.com

We need an updated, world class business card design. (See the attached existing card design). Please utilize BOTH sides of the card as shown and be creative with the layout. I do want the horse head icon to be positioned as it is with the existing card.

The remainder of the layout can be customized and I also want it vertically oriented.

Attached are the logo files and please use the colors as follows:
Green - #A5CE39
Tan - #CDBD99
Black

Feel free to play with the colors.

```html
<!DOCTYPE html>
<html lang="en">
<head>
<meta charset="utf-8">
<title>BrimFalcon Business Cards</title>
<link rel="stylesheet" href="https://fonts.googleapis.com/css2?family=Roboto+Slab:wght@400;700&display=swap">
<style>
  :root {
    --green: #a5ce39;
    --green-deep: #8fb52c;
    --tan: #cdbd99;
    --black: #111111;
    --white: #ffffff;
    --paper: #f4f4f2;
    --backdrop: #e6e8ea;
  }
  * { box-sizing: border-box; margin: 0; padding: 0; }
  html, body { width: 1200px; height: 900px; overflow: hidden; }
  body {
    background: var(--backdrop);
    font-family: "Roboto Slab", Georgia, serif;
    color: var(--black);
    position: relative;
  }
  .card {
    position: absolute;
    top: 100px;
    width: 400px;
    height: 700px;
    overflow: hidden;
    box-shadow: 0 10px 30px rgba(0,0,0,.18);
  }

  /* Front side */
  .card-front {
    left: 150px;
    background: linear-gradient(180deg, var(--tan) 0%, #bccb82 40%, var(--green) 100%);
  }
  .front-mark {
    position: absolute;
    left: 50%;
    top: 110px;
    transform: translateX(-50%);
    width: 210px;
    height: 210px;
    border-radius: 50%;
    background: var(--black);
  }
  .front-lockup {
    position: absolute;
    left: 0; right: 0;
    top: 400px;
    text-align: center;
  }
  .brand-name {
    font-weight: 700;
    font-size: 50px;
    letter-spacing: 1px;
    color: var(--black);
  }
  .brand-tagline {
    margin-top: 6px;
    font-weight: 400;
    font-size: 18px;
    letter-spacing: 5px;
  }

  /* Back side */
  .card-back {
    left: 650px;
    background: var(--paper);
  }
  .back-header {
    position: absolute;
    top: 0; left: 0; right: 0;
    height: 150px;
    display: flex;
    align-items: center;
    padding-left: 40px;
    gap: 14px;
  }
  .header-dot {
    width: 34px; height: 34px;
    border-radius: 50%;
    background: var(--black);
    flex: none;
  }
  .header-name { font-weight: 700; font-size: 28px; line-height: 1; }
  .header-tagline { font-size: 11px; letter-spacing: 3px; margin-top: 5px; }

  .name-band {
    position: absolute;
    top: 160px; left: 0; right: 0;
    height: 120px;
    background: var(--green);
    clip-path: polygon(0 18%, 100% 0, 100% 82%, 0 100%);
    padding: 38px 0 0 110px;
  }
  .rule {
    position: absolute;
    top: 150px; left: 0; right: 0;
    height: 4px;
    background: var(--green);
    transform: skewY(-2.6deg);
  }
  .person-name { font-weight: 700; font-size: 26px; letter-spacing: 1px; text-transform: uppercase; }
  .person-title { font-size: 17px; margin-top: 2px; }

  .icon-rail {
    position: absolute;
    left: 0; top: 270px; bottom: 0;
    width: 86px;
    background: linear-gradient(180deg, var(--green) 0%, var(--green-deep) 100%);
  }
  .bottom-band {
    position: absolute;
    left: 0; right: 0; bottom: 0;
    height: 36px;
    background: var(--green);
  }
  .contact-list {
    position: absolute;
    top: 335px; left: 0; right: 0;
    list-style: none;
  }
  .contact-item {
    display: flex;
    align-items: center;
    height: 68px;
  }
  .contact-icon {
    width: 86px;
    display: flex;
    justify-content: center;
  }
  .contact-icon svg { width: 38px; height: 38px; }
  .contact-text { padding-left: 22px; font-size: 17px; line-height: 1.25; }
</style>
</head>
<body>

<section class="card card-front" aria-label="Card front">
  <div class="front-mark"></div>
  <div class="front-lockup">
    <div class="brand-name">BrimFalcon</div>
    <div class="brand-tagline">Performance Driven EVs</div>
  </div>
</section>

<section class="card card-back" aria-label="Card back">
  <header class="back-header">
    <span class="header-dot"></span>
    <div>
      <div class="header-name">BrimFalcon</div>
      <div class="header-tagline">Performance Driven EVs</div>
    </div>
  </header>
  <div class="rule"></div>
  <div class="name-band">
    <div class="person-name">Dorian Maeve</div>
    <div class="person-title">President &amp; CEO</div>
  </div>
  <div class="icon-rail"></div>
  <div class="bottom-band"></div>

  <ul class="contact-list">
    <li class="contact-item">
      <span class="contact-icon">
        <svg viewBox="0 0 38 38" aria-hidden="true"><rect x="3" y="3" width="32" height="32" rx="7" fill="none" stroke="#111" stroke-width="2.5"/><path d="M13 11c2 0 3 3 3 4s-2 1-1 3 3 4 4 4 1-2 2-2 4 1 4 3-2 3-4 3c-5 0-11-6-11-11 0-2 1-4 3-4z" fill="#111"/></svg>
      </span>
      <span class="contact-text">306 555 0187</span>
    </li>
    <li class="contact-item">
      <span class="contact-icon">
        <svg viewBox="0 0 38 38" aria-hidden="true"><rect x="3" y="3" width="32" height="32" rx="7" fill="none" stroke="#111" stroke-width="2.5"/><rect x="10" y="12" width="18" height="14" fill="#111"/><path d="M10 12l9 8 9-8" fill="none" stroke="#a5ce39" stroke-width="1.8"/></svg>
      </span>
      <span class="contact-text">dorian@brimfalcon-example.com</span>
    </li>
    <li class="contact-item">
      <span class="contact-icon">
        <svg viewBox="0 0 38 38" aria-hidden="true"><rect x="3" y="3" width="32" height="32" rx="7" fill="none" stroke="#111" stroke-width="2.5"/><circle cx="19" cy="19" r="9" fill="none" stroke="#111" stroke-width="2"/><ellipse cx="19" cy="19" rx="4" ry="9" fill="none" stroke="#111" stroke-width="1.6"/><path d="M10 19h18M12 14h14M12 24h14" stroke="#111" stroke-width="1.4"/></svg>
      </span>
      <span class="contact-text">brimfalcon-example.com</span>
    </li>
    <li class="contact-item">
      <span class="contact-icon">
        <svg viewBox="0 0 38 38" aria-hidden="true"><rect x="3" y="3" width="32" height="32" rx="7" fill="none" stroke="#111" stroke-width="2.5"/><path d="M19 29c-5-6-7-9-7-12a7 7 0 0 1 14 0c0 3-2 6-7 12z" fill="#111"/><circle cx="19" cy="17" r="2.6" fill="#a5ce39"/></svg>
      </span>
      <span class="contact-text">Harlow Bend, Saskatchewan<br>canada</span>
    </li>
  </ul>
</section>

</body>
</html>
```